Redesign Fitness Photos for Facebook Ads Needed

We are a fun, energetic, group fitness facility that needs to have a few (3) photos doctored up and turned into ads for Facebook & Instagram.
I would like the photos to be doctored up so that they are clear, bright, energetic.  Feel free to manipulate the photos, backgrounds, cropping, cutting as needed.
I would like to include text on photos:
Pulsora
New Year
Challenge
* Fitness Training  * Nutritional Support * Motivation & Support
Join Now
The text should be roughly the size of the examples included in order to comply with facebooks text size requirements
I have included 3 examples of another gyms ads which I like how the images are eye catching and text is clearly visible and pops with color.
Although I have attached multiple images that can be used,  I am only looking for 3 completed designs to be used for ads.

You choose the images that you feel you can modify the best.
I look forward to seeing your design.
Thank you.

```html
<!DOCTYPE html>
<html lang="en">
<head>
<meta charset="utf-8">
<title>Pulsora – New Year Challenge</title>
<link rel="stylesheet" href="https://fonts.googleapis.com/css2?family=Ubuntu:wght@500;700&family=Oswald:wght@500&display=swap">
<style>
  :root {
    --night: #0d1026;
    --deep-blue: #1b2c8f;
    --violet: #3a2f6b;
    --gold: #ffc93c;
    --amber: #f7a928;
    --orange: #ef7b2c;
    --white: #ffffff;
    --ink: #1a1410;
    --skin: #b9805f;
    --shadow-skin: #5e3a2c;
    --haze: rgba(200,200,210,0.35);
  }
  html, body {
    margin: 0;
    padding: 0;
    width: 1200px;
    height: 1200px;
    overflow: hidden;
    background: var(--night);
  }
  .ad {
    position: relative;
    width: 1200px;
    height: 1200px;
    overflow: hidden;
    font-family: "Ubuntu", sans-serif;
  }
  .ad__studio {
    position: absolute;
    inset: 0;
    background:
      radial-gradient(ellipse 300px 260px at 120px 300px, var(--haze), transparent 70%),
      radial-gradient(ellipse 420px 300px at 1000px 1080px, var(--haze), transparent 70%),
      radial-gradient(ellipse 700px 520px at 480px 340px, rgba(40,70,230,0.85), transparent 70%),
      radial-gradient(ellipse 500px 400px at 200px 800px, rgba(20,40,150,0.6), transparent 70%),
      linear-gradient(160deg, var(--deep-blue) 0%, #1d1f5e 50%, var(--night) 100%);
  }
  .ad__column {
    position: absolute;
    left: 1033px;
    top: 233px;
    width: 78px;
    height: 890px;
    background: linear-gradient(180deg, rgba(220,170,40,0.8), rgba(170,130,40,0.55));
  }
  .ad__athlete {
    position: absolute;
    left: 420px;
    top: 150px;
    width: 640px;
    height: 1080px;
    border-radius: 46% 46% 30% 30% / 30% 30% 20% 20%;
    background:
      radial-gradient(ellipse 150px 180px at 330px 420px, var(--skin), transparent 75%),
      radial-gradient(ellipse 260px 220px at 380px 620px, rgba(185,128,95,0.85), transparent 75%),
      radial-gradient(ellipse 200px 320px at 220px 260px, rgba(185,128,95,0.7), transparent 75%),
      radial-gradient(ellipse 320px 300px at 380px 880px, rgba(40,40,60,0.95), transparent 75%),
      radial-gradient(ellipse 340px 500px at 330px 560px, var(--shadow-skin), transparent 80%);
    filter: blur(6px);
  }
  .ad__stripes {
    position: absolute;
    left: 0;
    top: 0;
  }
  .brand-panel {
    position: absolute;
    left: 575px;
    top: -10px;
    width: 640px;
    height: 243px;
    border-bottom-left-radius: 175px;
    background: linear-gradient(100deg, #d9a22a 0%, #e8a43c 55%, #c9772e 100%);
  }
  .brand-panel__name {
    position: absolute;
    left: 136px;
    top: 28px;
    margin: 0;
    font-weight: 700;
    font-size: 108px;
    line-height: 1;
    color: var(--white);
  }
  .brand-panel__tagline {
    position: absolute;
    left: 140px;
    top: 134px;
    margin: 0;
    font-weight: 500;
    font-size: 25px;
    line-height: 1;
    letter-spacing: 5px;
    color: var(--white);
  }
  .corner {
    position: absolute;
    left: 0;
    bottom: 0;
  }
  .dots {
    position: absolute;
    left: 300px;
    top: 1040px;
    width: 300px;
    height: 160px;
    background: rgba(255,255,255,0.22);
    clip-path: polygon(45% 0, 55% 0, 100% 100%, 0 100%);
  }
  .headline {
    margin: 0;
    font-weight: 700;
    font-size: 75px;
    line-height: 1;
    color: var(--gold);
  }
  .headline__line {
    position: absolute;
    left: 52px;
  }
  .headline__line--first { top: 452px; }
  .headline__line--second { top: 557px; }
  .benefits {
    position: absolute;
    left: 46px;
    top: 650px;
    margin: 0;
    padding: 0;
    list-style: none;
    font-weight: 700;
    font-size: 44px;
    line-height: 68px;
    color: var(--white);
  }
  .benefits li::before { content: "* "; }
  .cta {
    position: absolute;
    left: 292px;
    top: 917px;
    width: 308px;
    height: 122px;
    border-radius: 61px;
    background: linear-gradient(90deg, var(--orange) 0%, var(--gold) 100%);
    display: flex;
    align-items: center;
    justify-content: center;
    font-family: "Oswald", sans-serif;
    font-weight: 500;
    font-size: 38px;
    color: var(--ink);
    text-decoration: none;
  }
</style>
</head>
<body>
<main class="ad">
  <div class="ad__studio" role="img" aria-label="Blue-lit group fitness studio with haze drifting across the room and other members training behind"></div>
  <div class="ad__column"></div>
  <div class="ad__athlete" role="img" aria-label="Woman in a low lunge pressing a dumbbell overhead, wearing a dark tank top and patterned leggings"></div>

  <svg class="ad__stripes" width="560" height="100" viewBox="0 0 560 100" aria-hidden="true">
    <g stroke="#c99a3a" stroke-width="12" opacity="0.55">
      <line x1="10" y1="95" x2="70" y2="0"/>
      <line x1="70" y1="95" x2="130" y2="0"/>
      <line x1="130" y1="95" x2="190" y2="0"/>
      <line x1="190" y1="95" x2="250" y2="0"/>
      <line x1="250" y1="95" x2="310" y2="0"/>
      <line x1="310" y1="95" x2="370" y2="0"/>
      <line x1="370" y1="95" x2="430" y2="0"/>
      <line x1="430" y1="95" x2="490" y2="0"/>
    </g>
  </svg>

  <svg class="corner" width="460" height="460" viewBox="0 0 460 460" aria-hidden="true">
    <defs>
      <linearGradient id="corner-fill" x1="0" y1="0" x2="1" y2="1">
        <stop offset="0" stop-color="#e9a52e"/>
        <stop offset="1" stop-color="#d8782c"/>
      </linearGradient>
    </defs>
    <polygon points="0,40 0,460 420,460" fill="rgba(20,15,10,0.55)"/>
    <polygon points="0,127 0,460 333,460" fill="url(#corner-fill)" opacity="0.92"/>
  </svg>

  <div class="dots" role="img" aria-label="Dot pattern accent"></div>

  <header class="brand-panel">
    <p class="brand-panel__name">Pulsora</p>
    <p class="brand-panel__tagline">Personal Group Training</p>
  </header>

  <h1 class="headline">
    <span class="headline__line headline__line--first">New Year</span>
    <span class="headline__line headline__line--second">Challenge</span>
  </h1>

  <ul class="benefits">
    <li>Fitness Training</li>
    <li>Nutritional Support</li>
    <li>Motivation &amp; Support</li>
  </ul>

  <a class="cta">JOIN NOW</a>
</main>
</body>
</html>
```